Business Card Design Can you design a business card design? Looking for something unique and differe

Can you design a business card design? Looking for something unique and different. Can you design a business card design? Looking for something unique and different.Can you design a business card design? Looking for something unique and different.Can you design a business card design? Looking for something unique and different.Can you design a business card design? Looking for something unique and different.Can you design a business card design? Looking for something unique and different.

Industry/Entity Type

Business

Contact Information for Business Card

Can you design a business card design? Looking for something unique and different.

Font styles to use
Serif

```html
<!DOCTYPE html>
<html lang="en">
<head>
<meta charset="utf-8">
<title>Qorvelin Business Card</title>
<link href="https://fonts.googleapis.com/css2?family=Source+Sans+3:wght@400;600&display=swap" rel="stylesheet">
<style>
  :root {
    --backdrop: #8b8b8b;
    --card-black: #000000;
    --panel-black: #121212;
    --lilac: #a184b6;
    --white: #ffffff;
  }
  * { box-sizing: border-box; margin: 0; padding: 0; }
  html, body {
    width: 1200px; height: 900px; overflow: hidden;
    background: var(--backdrop);
    font-family: "Source Sans 3", sans-serif;
  }
  .sheet {
    width: 1200px; height: 900px;
    display: flex; flex-direction: column;
    align-items: center; justify-content: center; gap: 44px;
  }
  .card {
    position: relative;
    width: 660px; height: 378px;
    background: var(--card-black);
    overflow: hidden;
    box-shadow: 0 6px 18px rgba(0,0,0,.25);
  }
  .card__stripe {
    position: absolute; left: 0; right: 0; bottom: 0; height: 62px;
    background: var(--lilac);
    border-top: 9px solid var(--white);
  }

  /* front */
  .front__brand {
    position: absolute; left: 0; right: 0; top: 118px;
    display: flex; align-items: center; justify-content: center; gap: 16px;
  }
  .brand-dot { width: 22px; height: 22px; background: var(--lilac); }
  .brand-name {
    color: var(--lilac); font-weight: 600; font-size: 50px; letter-spacing: .5px;
    line-height: 1.1;
  }

  /* back */
  .back__brand {
    position: absolute; left: 40px; top: 64px;
    display: flex; align-items: center; gap: 12px;
  }
  .back__brand .brand-name { font-size: 40px; }
  .back__brand .brand-dot { width: 18px; height: 18px; }
  .back__person {
    position: absolute; right: 40px; top: 60px; text-align: right; color: var(--white);
  }
  .person-name {
    color: var(--lilac); font-weight: 600; font-size: 22px; letter-spacing: 1px;
  }
  .person-role { font-size: 18px; margin-top: 2px; }
  .back__panel {
    position: absolute; left: 0; right: 0; top: 170px; height: 146px;
    background: var(--panel-black);
    display: grid; grid-template-columns: 1.25fr 1fr 1.15fr;
    padding: 24px 30px 0 40px;
    color: var(--white); font-size: 15.5px; line-height: 1.6;
  }
  .contact-group { display: flex; flex-direction: column; }
  .contact-group--phones { padding-top: 26px; }
  .contact-group--web { padding-top: 56px; }
  .contact-line { display: flex; align-items: flex-start; gap: 8px; }
  .contact-icon { width: 13px; height: 13px; margin-top: 6px; flex: none; fill: var(--lilac); }
</style>
</head>
<body>
<main class="sheet">

  <section class="card card--front" aria-label="Card front">
    <div class="front__brand">
      <span class="brand-dot"></span>
      <span class="brand-name">Qorvelin</span>
    </div>
    <div class="card__stripe"></div>
  </section>

  <section class="card back" aria-label="Card back">
    <div class="back__brand">
      <span class="brand-dot"></span>
      <span class="brand-name">Qorvelin</span>
    </div>

    <div class="back__person">
      <p class="person-name">DANIEL HART</p>
      <p class="person-role">Managing Director</p>
    </div>

    <div class="back__panel">
      <div class="contact-group contact-group--address">
        <p class="contact-line">
          <svg class="contact-icon" viewBox="0 0 12 12"><path d="M6 0a4 4 0 0 0-4 4c0 3 4 8 4 8s4-5 4-8a4 4 0 0 0-4-4zm0 5.6A1.6 1.6 0 1 1 6 2.4a1.6 1.6 0 0 1 0 3.2z"/></svg>
          <span>1234, Address Goes Here,<br>Country Name, 123456</span>
        </p>
      </div>
      <div class="contact-group contact-group--phones">
        <p class="contact-line">
          <svg class="contact-icon" viewBox="0 0 12 12"><path d="M1 4c0-2 2-3 5-3s5 1 5 3H8.5V3h-5v1zM2 5h8l1 6H1z"/></svg>
          <span>123.456.7890</span>
        </p>
        <p class="contact-line">
          <svg class="contact-icon" viewBox="0 0 12 12"><path d="M3 0h6v4H3zM1 4h10v8H1zm2 2v2h6V6z"/></svg>
          <span>123.456.7890</span>
        </p>
      </div>
      <div class="contact-group contact-group--web">
        <p class="contact-line">
          <svg class="contact-icon" viewBox="0 0 12 12"><path d="M0 2h12v8H0zm1 1v.4l5 3.4 5-3.4V3z"/></svg>
          <span>info@youremail.com</span>
        </p>
        <p class="contact-line">
          <svg class="contact-icon" viewBox="0 0 12 12"><path d="M5 7 7 5l1 1-2 2zM2 7l2-2 1 1-2 2 1 1 2-2 1 1-2 2a1.4 1.4 0 0 1-2 0L2 9a1.4 1.4 0 0 1 0-2zm5-4 1 1-1 1-1-1zm1-2a1.4 1.4 0 0 1 2 0l1 1a1.4 1.4 0 0 1 0 2L9 7 8 6l2-2-1-1-2 2-1-1z"/></svg>
          <span>www.website.com</span>
        </p>
      </div>
    </div>

    <div class="card__stripe"></div>
  </section>

</main>
</body>
</html>
```